Website design for a high-end equestrian business

Design a website to replace current one. Clean, simple, elegant design. I run a business training show jumping riders and horses, as well as buying and selling high quality horses. I run my business from a beautiful yard in Co. Kildare, Ireland. Reference to Ireland and quality sport horses is important in the website.

Current website is www.orlathornbury.com. One page in particular that I need is a "Sport Horses" page as well as a "References" page. Layout for each to be similar to this one - https://www.brackenleaze.net/en/sporthorses

Another website I like the feel of is www.topcanterstable.com
Colour theme to be charcoal grey with elements of lighter grey and cream, as per logo. Charcoal grey to be somewhat transparent, otherwise it takes over too much. Cream colour is also to be subtle and not too beige.

Please note that Thornbury is one word.

Please note there are new photographs with which to work if desired.

Sick

Target Market(s)

Upmarket clients seeking high quality coaching services and high quality show jumping horses

Number of Pages Required

2 page

Font styles to use
Serif
Sans Serif

Colors

Designer to choose only greyscale colors for use in the design.

Requirements
Must have
• A clean, simple, elegant look to the final design. OVerall theme colours must be subtle and include charcoal grey, light grey and cream. A design that will work well for mobile also. Please include only photographs provided or on the old website.
Nice to have
• artistically integrated photographs. use of the logo.
Should not have
• Anything fussy.

```html
<!DOCTYPE html>
<html lang="en">
<head>
<meta charset="utf-8">
<title>Orla Thornbury – Website Design</title>
<link href="https://fonts.googleapis.com/css2?family=Noto+Serif:wght@400;700&display=swap" rel="stylesheet">
<style>
  :root {
    --board: #c9b47e;
    --title-cream: #fdf7ea;
    --white: #ffffff;
    --ink: #1c1c1c;
    --charcoal: #555555;
    --muted: #8a8a8a;
    --nav: #555555;
    --ring: #d3d3d3;
    --button-gold: #c8b27a;
    --button-grey: #6b6b6b;
  }
  * { margin: 0; padding: 0; box-sizing: border-box; }
  html, body { width: 1200px; height: 1200px; overflow: hidden; }
  body {
    background: var(--board);
    font-family: "Noto Serif", Georgia, serif;
    position: relative;
    color: var(--ink);
  }
  .board-title {
    position: absolute; left: 720px; width: 410px; top: 136px;
    text-align: center; color: var(--title-cream);
    font-weight: 700; font-size: 50px; line-height: 56px;
  }
  .page { position: absolute; background: var(--white); overflow: hidden; }
  .page--home { left: 89px; top: 118px; width: 480px; height: 1100px; }
  .page--horses { left: 649px; top: 328px; width: 530px; height: 849px; }

  .site-header { position: absolute; left: 0; top: 0; width: 100%; background: var(--white);
    border-bottom: 1px solid #e6e6e6; z-index: 3; }
  .page--home .site-header { height: 39px; }
  .page--horses .site-header { height: 43px; }
  .brand { position: absolute; top: 50%; transform: translateY(-50%);
    font-size: 12px; font-weight: 400; color: var(--charcoal); display: flex; align-items: center; gap: 3px; }
  .brand-dot { width: 6px; height: 6px; border-radius: 50%; background: var(--button-gold); }
  .page--home .brand { left: 37px; }
  .page--horses .brand { left: 41px; }
  .main-nav { position: absolute; top: 50%; transform: translateY(-50%);
    display: flex; justify-content: space-between; font-size: 6.3px; font-weight: 700; color: var(--nav); }
  .page--home .main-nav { left: 134px; width: 300px; }
  .page--horses .main-nav { left: 148px; width: 330px; font-size: 7px; }
  .menu-icon { position: absolute; top: 50%; transform: translateY(-50%); width: 9px; }
  .page--home .menu-icon { left: 533px; left: 448px; }
  .page--horses .menu-icon { left: 495px; }
  .menu-icon span { display: block; height: 1.4px; background: #333; margin: 1.6px 0; }

  /* home hero */
  .hero-ring { position: absolute; left: 206px; top: -8px; width: 342px; height: 342px;
    border-radius: 50%; background: var(--ring); }
  .hero-photo { position: absolute; left: 260px; top: 56px; width: 232px; height: 232px; border-radius: 50%;
    background: radial-gradient(circle at 55% 45%, #7a5a3a 0 12%, #4f9a2c 30%, #3f8a22 70%, #2f6d1a 100%); }
  .hero-intro { position: absolute; left: 56px; top: 97px; }
  .hero-kicker { font-size: 6.5px; font-weight: 700; }
  .hero-place { margin-top: 4px; font-size: 17px; line-height: 18px; font-weight: 700; color: var(--charcoal); }
  .btn-explore { position: absolute; left: 56px; top: 160px; width: 117px; height: 24px; border-radius: 12px;
    background: var(--button-gold); color: var(--white); font-size: 12px; font-weight: 700;
    display: flex; align-items: center; justify-content: center; }

  .livery-photo { position: absolute; left: 29px; top: 298px; width: 200px; height: 200px; border-radius: 50%;
    background: linear-gradient(180deg, #8fbde8 0%, #b9d4ec 35%, #8a6a48 55%, #c9b79a 80%, #a9a08a 100%); }
  .livery-text { position: absolute; left: 254px; top: 385px; width: 200px; }
  .livery-text h2 { font-size: 23px; font-weight: 700; line-height: 26px; }
  .livery-text p { margin-top: 14px; font-size: 10.3px; line-height: 14px; }

  .horses-band { position: absolute; left: 0; top: 548px; width: 480px; height: 259px;
    background: linear-gradient(100deg, #3b3a33 0%, #4a4236 35%, #3a3a30 60%, #2e3528 100%); }
  .horses-band-text { position: absolute; left: 54px; top: 105px; color: var(--white); }
  .horses-band-text h2 { font-size: 23px; font-weight: 700; line-height: 26px; margin-left: 2px; }
  .horses-band-text p { margin-top: 6px; font-size: 13px; line-height: 17px; width: 230px; }

  .about { position: absolute; left: 0; top: 850px; width: 480px; text-align: center; }
  .about h2 { font-size: 24px; font-weight: 700; color: #666; line-height: 30px; }
  .about p { margin: 14px auto 0; width: 372px; font-size: 13.4px; line-height: 19.3px; color: var(--muted); }

  /* sport horses page */
  .sport-hero { position: absolute; left: 0; top: 43px; width: 530px; height: 254px;
    background: linear-gradient(180deg, #3f4658 0%, #5a5050 30%, #6b4a30 55%, #7a6248 75%, #8f8070 100%); }
  .sport-hero h1 { position: absolute; left: 45px; top: 94px; color: var(--white);
    font-size: 27px; line-height: 25px; font-weight: 700; }
  .collection-title { position: absolute; left: 0; width: 100%; top: 330px; text-align: center;
    font-size: 19px; font-weight: 700; }
  .horse-card { position: absolute; width: 133px; text-align: center; }
  .horse-card .thumb { width: 133px; height: 98px; position: relative; }
  .horse-card .name { margin-top: 14px; font-size: 7px; font-weight: 700; }
  .play { position: absolute; right: 14px; bottom: 3px; width: 13px; height: 13px; }
  .btn-load { position: absolute; left: 191px; top: 754px; width: 147px; height: 27px; border-radius: 4px;
    background: var(--button-grey); color: var(--white); font-size: 13px; font-weight: 700;
    display: flex; align-items: center; justify-content: center; }

  .site-footer-note { position: absolute; left: 672px; top: 1190px; font-size: 6.5px; color: var(--ink); }
  .social { position: absolute; top: 1187px; width: 24px; height: 24px; border-radius: 50%; background: #4a4a4a; }
</style>
</head>
<body>

<h1 class="board-title">Orla<br>Thornbury</h1>

<section class="page page--home">
  <header class="site-header">
    <div class="brand"><span>OT</span><span class="brand-dot"></span></div>
    <nav class="main-nav"><span>Home</span><span>Horses</span><span>References</span><span>Training</span><span>News</span><span>Blog</span><span>Sponsors</span><span>FairRide</span></nav>
    <div class="menu-icon"><span></span><span></span><span></span></div>
  </header>

  <div class="hero-ring"></div>
  <div class="hero-photo" role="img" aria-label="Rider and bay horse clearing a green planted fence on a grass arena"></div>
  <div class="hero-intro">
    <p class="hero-kicker">Orla Thornbury at</p>
    <p class="hero-place">BALLYRANE,<br>CO.KILDARE</p>
  </div>
  <div class="btn-explore">Explore</div>

  <div class="livery-photo" role="img" aria-label="Rider and chestnut horse jumping a coloured fence under a blue sky"></div>
  <div class="livery-text">
    <h2>Livery &amp; training</h2>
    <p>Top class training and livery facilities in Kildare, a short distance from many of the bigger competition venue</p>
  </div>

  <div class="horses-band" role="img" aria-label="Rider in helmet standing beside her saddled bay horse, darkened">
    <div class="horses-band-text">
      <h2>Horses</h2>
      <p>Orla trains and competes quality horses of all ages</p>
    </div>
  </div>

  <div class="about">
    <h2>About Orla</h2>
    <p>From Ballyrane in Co. Kildare, Orla is 31 years old and has been passionate about horses since she was a child. Over the years she has achieved many successes with a variety of equine partners, from Pony National Champion two years running on Harbour Light to Senior National Champion and Nations Cup team-member on Cloudburst in more recent years. Having completed her studies in Larchfield College Dublin in 2010, her main focus now is running a small private show jumping stable from her home in Ballyrane, producing younger horses right up the ranks to international level.</p>
  </div>
</section>

<section class="page page--horses">
  <header class="site-header">
    <div class="brand"><span>OT</span><span class="brand-dot"></span></div>
    <nav class="main-nav"><span>Home</span><span>Horses</span><span>References</span><span>Training</span><span>News</span><span>Blog</span><span>Sponsors</span><span>FairRide</span></nav>
    <div class="menu-icon"><span></span><span></span><span></span></div>
  </header>

  <div class="sport-hero" role="img" aria-label="Horse and rider jumping a wooden fence in front of a crowded grandstand">
    <h1>SPORT<br>HORSES</h1>
  </div>

  <h2 class="collection-title">Sport Collection</h2>

  <div class="horse-card" style="left:38px; top:401px;">
    <div class="thumb" role="img" aria-label="Bay horse jumping a green fence on grass" style="background:linear-gradient(180deg,#5aa82e,#3f8a22 70%,#2d6b1a);">
      <svg class="play" viewBox="0 0 14 14"><circle cx="7" cy="7" r="7" fill="#fff"/><path d="M5.3 4.2 L10 7 L5.3 9.8Z" fill="#111"/></svg>
    </div>
    <p class="name">Ardmore</p>
  </div>
  <div class="horse-card" style="left:198px; top:401px;">
    <div class="thumb" role="img" aria-label="Rider standing with her bay horse" style="background:linear-gradient(90deg,#5a4a38,#6c5a44 50%,#8ea08a);"></div>
    <p class="name">Corrib</p>
  </div>
  <div class="horse-card" style="left:358px; top:401px;">
    <div class="thumb" role="img" aria-label="Horse jumping a red fence in front of white marquees" style="background:linear-gradient(180deg,#6fa0d8,#7aa05a 40%,#c04040 60%,#d9cbb0);"></div>
    <p class="name">BLT Fenwick</p>
  </div>

  <div class="horse-card" style="left:38px; top:574px;">
    <div class="thumb" role="img" aria-label="Horse jumping wooden fence before a full grandstand" style="background:linear-gradient(180deg,#4a4a5a,#6a5040 50%,#b08050 75%,#d0c0a8);"></div>
    <p class="name">BLT Glenmore Gambit</p>
  </div>
  <div class="horse-card" style="left:200px; top:574px;">
    <div class="thumb" role="img" aria-label="Horse jumping a blue and yellow fence in a stadium" style="background:linear-gradient(180deg,#5a5a6a,#3a5aa0 50%,#e0c040 75%,#9aa0b0);"></div>
    <p class="name">Willow Starling</p>
  </div>
  <div class="horse-card" style="left:358px; top:574px;">
    <div class="thumb" role="img" aria-label="Horse jumping in front of a scoreboard" style="background:linear-gradient(180deg,#a8b0b8,#6a5040 50%,#3a4a6a 75%,#5a6a50);"></div>
    <p class="name">Quillamara</p>
  </div>

  <div class="btn-load">Load More</div>
</section>

<p class="site-footer-note">Copyright 2018 All rights reserved</p>
<div class="social" style="left:1040px;" role="img" aria-label="Social link"></div>
<div class="social" style="left:1078px;" role="img" aria-label="Social link"></div>
<div class="social" style="left:1116px;" role="img" aria-label="Social link"></div>

</body>
</html>
```